Silver Bloom Marisol's Cleaning Service Business Cards Project

A business card with all contact details with logo design on there (already have a logo) eye catching Logo and contact info on one side, full logo on the back, must target upper class residential and corporate companies, fitness companies, still keep it on the feminine side of things , must look elegant

Target Market(s)

Upper class homes and corporate companies

Industry/Entity Type

Cleaning Service

Contact Information for Business Card

Name: Marisol Quenby
Position: Director
ABN: 31647209853
Email: marisolssilvercleaning@tidymail.example
Number: 0417906354

Font styles to use
Decorative

Colors

Designer to choose colors to be used in the design.

Requirements
Must have
• Available Sydney Wide, contact info and logo on one side, full logo on the back
Nice to have
• Professional appearance
Should not have
• Cheap advert looking stuff

```html
<!DOCTYPE html>
<html lang="en">
<head>
<meta charset="utf-8">
<title>Silver Bloom – Business Card</title>
<link rel="stylesheet" href="https://fonts.googleapis.com/css2?family=Cinzel:wght@500&family=Oswald:wght@400&family=Roboto:wght@400&display=swap">
<style>
  :root {
    --page-bg: #d9d4cc;
    --card-frost: #ece9e3;
    --card-band: #2b2d32;
    --ink-dark: #2a2a2c;
    --ink-muted: #5d5b57;
    --teal: #4fb3a4;
    --teal-deep: #2f9486;
    --cream: #e6dccb;
    --sand: #d4c5a8;
    --contact: #e8e4dc;
  }
  * { margin: 0; padding: 0; box-sizing: border-box; }
  html, body {
    width: 1200px; height: 1047px; overflow: hidden;
    background: var(--page-bg);
  }
  .card {
    position: absolute; left: 100px; top: 243px;
    width: 1000px; height: 560px;
    border-radius: 28px; overflow: hidden;
    background: var(--card-frost);
    box-shadow: 0 18px 40px rgba(0,0,0,.18);
  }
  .card-shapes { position: absolute; inset: 0; }
  .brand {
    position: absolute; left: 0; right: 0; top: 92px;
    text-align: center; color: var(--ink-dark);
  }
  .brand-mark {
    display: block; width: 14px; height: 14px; margin: 0 auto 14px;
    border: 2px solid var(--ink-dark); border-radius: 50%;
  }
  .brand-name {
    font-family: "Cinzel", serif; font-weight: 500;
    font-size: 30px; letter-spacing: 2px;
  }
  .brand-tagline {
    font-family: "Cinzel", serif; font-weight: 500;
    font-size: 11px; letter-spacing: 3.5px; margin-top: 4px;
  }
  .holder {
    position: absolute; left: 60px; top: 400px; width: 350px; text-align: right;
  }
  .holder-name {
    font-family: "Oswald", sans-serif; font-weight: 400;
    font-size: 50px; letter-spacing: 3px; line-height: 1;
    color: var(--sand); text-transform: uppercase; text-align: left;
    white-space: nowrap;
  }
  .holder-role {
    font-family: "Roboto", sans-serif; font-size: 21px;
    color: #bdb6aa; margin-top: 8px;
  }
  .divider {
    position: absolute; left: 440px; top: 400px;
    width: 2px; height: 95px; background: #8d877d;
  }
  .contacts {
    position: absolute; left: 475px; top: 398px;
    font-family: "Roboto", sans-serif; font-size: 21px; color: var(--contact);
    list-style: none;
  }
  .contacts li { display: flex; align-items: center; height: 38px; }
  .contacts svg { width: 16px; height: 16px; margin-right: 14px; flex: none; }
</style>
</head>
<body>
  <article class="card">
    <svg class="card-shapes" viewBox="0 0 1000 560" width="1000" height="560">
      <defs>
        <linearGradient id="vine-tone" x1="0" y1="0" x2="0" y2="1">
          <stop offset="0" stop-color="#4fb3a4" stop-opacity="0"/>
          <stop offset="0.35" stop-color="#4fb3a4" stop-opacity="0.55"/>
          <stop offset="0.7" stop-color="#2f9486" stop-opacity="0.6"/>
          <stop offset="1" stop-color="#2f9486" stop-opacity="0"/>
        </linearGradient>
      </defs>
      <path class="dark-band" fill="var(--card-band)"
        d="M0 270 C120 250 150 330 250 340 C380 350 420 300 500 300 C580 300 620 350 750 340 C850 330 880 250 1000 270 L1000 560 L0 560 Z"/>
      <rect x="0" y="200" width="1000" height="170" fill="url(#vine-tone)"
        role="img" aria-label="Teal scrolling vine ornament with leaves spanning the card"/>
    </svg>

    <header class="brand">
      <span class="brand-mark"></span>
      <div class="brand-name">SILVER BLOOM</div>
      <div class="brand-tagline">MARISOL'S CLEANING SERVICE</div>
    </header>

    <div class="holder">
      <div class="holder-name">Marisol Quenby</div>
      <div class="holder-role">Director</div>
    </div>
    <div class="divider"></div>

    <ul class="contacts">
      <li>ABN: 31647209853</li>
      <li>
        <svg viewBox="0 0 16 16" aria-hidden="true"><path fill="#e8e4dc" d="M3.5 1.5l2.2 2.4-1.2 1.6c.8 1.9 2.1 3.2 4 4l1.6-1.2 2.4 2.2-1.4 2.3C6.8 12.6 3.4 9.2 1.2 3z"/></svg>
        0417906354
      </li>
      <li>
        <svg viewBox="0 0 16 16" aria-hidden="true"><rect x="1.5" y="3.5" width="13" height="9" fill="none" stroke="#e8e4dc" stroke-width="1.4"/><path d="M1.5 3.5l6.5 5 6.5-5" fill="none" stroke="#e8e4dc" stroke-width="1.4"/></svg>
        marisolssilvercleaning@tidymail.example
      </li>
    </ul>
  </article>
</body>
</html>
```